Road Construction Company needs business cards

We would like a new business card designed for our business.

We're a road construction company based in Qld, Australia.

Can the business card please have the following information on it.

Name: Warren Halbeck
Position: General Manager
Phone: 0472 915 348
Email: Warren.halbeck@tovrin.com.au
Address: 87 Marrow Ave, Pendlebay, QLD, 4023
Website: www.tovrin.com.au

Visually we'd like the card to be professional and simple.

Attached is our logo.

Our website is www.tovrin.com.au

Target Market(s)

Men aged 25-60

Contact Information for Business Card

As listed in project description

Font styles to use
Serif

Requirements
Must have
• Large logo on back of card

```html
<!DOCTYPE html>
<html lang="en">
<head>
<meta charset="utf-8">
<title>Tovrin – Business Card</title>
<link rel="stylesheet" href="https://fonts.googleapis.com/css2?family=Open+Sans:wght@400;600;700&display=swap">
<style>
  :root {
    --backdrop: #1c1d21;
    --card: #222126;
    --brand-blue: #1558b0;
    --band-blue: #3fa9dc;
    --text-light: #f2f2f2;
    --divider: #ffffff;
  }
  * { box-sizing: border-box; margin: 0; padding: 0; }
  html, body {
    width: 1200px; height: 780px; overflow: hidden;
    background: var(--backdrop);
    font-family: "Open Sans", Arial, sans-serif;
  }
  .sheet {
    width: 1200px; height: 780px;
    display: flex; align-items: center; justify-content: center; gap: 50px;
  }
  .card {
    position: relative;
    width: 540px; height: 310px;
    background: var(--card);
    border-radius: 22px;
    overflow: hidden;
    box-shadow: 0 0 0 3px var(--band-blue);
  }
  .brand-name {
    color: var(--brand-blue);
    font-weight: 700;
    letter-spacing: 2px;
    line-height: 1;
  }
  /* Front */
  .card-front .brand-name {
    position: absolute; left: 34px; top: 48px;
    font-size: 46px;
  }
  .card-front .divider {
    position: absolute; left: 210px; top: 60px;
  }
  .contact {
    position: absolute; left: 300px; top: 72px;
    color: var(--text-light);
  }
  .contact-name {
    color: var(--brand-blue);
    font-weight: 600; font-size: 28px; line-height: 1.1;
  }
  .contact-role { font-size: 16px; margin-bottom: 14px; }
  .contact-list { list-style: none; font-size: 14px; line-height: 1.65; }
  .contact-list li { display: flex; align-items: center; gap: 8px; }
  .contact-list svg { width: 13px; height: 13px; flex: none; }
  .address-band {
    position: absolute; left: 0; right: 0; bottom: 0; height: 50px;
    background: var(--band-blue);
    color: var(--text-light);
    font-size: 18px;
    display: flex; align-items: center; padding-left: 40px;
  }
  /* Back */
  .card-back { display: flex; align-items: center; justify-content: center; }
  .card-back .brand-name { font-size: 104px; letter-spacing: 6px; }
</style>
</head>
<body>
<main class="sheet">
  <section class="card card-front" aria-label="Business card front">
    <div class="brand-name">TOVRIN</div>
    <svg class="divider" width="70" height="190" viewBox="0 0 70 190" aria-hidden="true">
      <line x1="68" y1="2" x2="2" y2="188" stroke="var(--divider)" stroke-width="2"/>
    </svg>
    <div class="contact">
      <div class="contact-name">Warren Halbeck</div>
      <div class="contact-role">General Manager</div>
      <ul class="contact-list">
        <li>
          <svg viewBox="0 0 16 16" aria-hidden="true"><path d="M4 1l3 3-2 2c1 2 3 4 5 5l2-2 3 3-2 3C7 15 1 9 1 3z" fill="var(--band-blue)"/></svg>
          0472 915 348
        </li>
        <li>
          <svg viewBox="0 0 16 16" aria-hidden="true"><circle cx="8" cy="8" r="7" fill="none" stroke="var(--band-blue)" stroke-width="1.6"/><path d="M1 8h14M8 1c3 3 3 11 0 14M8 1c-3 3-3 11 0 14" fill="none" stroke="var(--band-blue)" stroke-width="1.2"/></svg>
          www.tovrin.com.au
        </li>
        <li>
          <svg viewBox="0 0 16 16" aria-hidden="true"><rect x="1" y="3" width="14" height="10" rx="1" fill="none" stroke="var(--band-blue)" stroke-width="1.6"/><path d="M1 4l7 5 7-5" fill="none" stroke="var(--band-blue)" stroke-width="1.4"/></svg>
          Warren.halbeck@tovrin.com.au
        </li>
      </ul>
    </div>
    <div class="address-band">87 Marrow Ave, Pendlebay, QLD, 4023</div>
  </section>

  <section class="card card-back" aria-label="Business card back">
    <div class="brand-name">TOVRIN</div>
  </section>
</main>
</body>
</html>
```